Marlow Estate Fixers (Handyman / Home Improvement Company)

Looking for a double sided professional looking business card with Logo attached to be highlighted on one side and throwing in an image of a handyman as an option would be nice to see as well. We are a company focused on providing quality Handyman and Home improvement services in a timely manner that is done right the first time with integrity

Industry/Entity Type

Handyman / Home Improvement

Contact Information for Business Card

(LOGO, Name, Mobile and office phone numbers, email) on front side of card, (the words "The SOLUTION to all of your Handyman and Home Improvement needs" followed by "Family Owned and Operated" at the very bottom) on the back.

Colors
EB3D1F
EC4F4E
F09395
F8D3D4
FCEDEE

Requirements
Must have
• Red, Gray, Black Color scheme
Should not have
• No Yellow or Blue colors

```html
<!DOCTYPE html>
<html lang="en">
<head>
<meta charset="utf-8">
<title>Marlow Estate Fixers – Business Card</title>
<link href="https://fonts.googleapis.com/css2?family=Poppins:wght@400;500;600&display=swap" rel="stylesheet">
<style>
  :root {
    --page: #f1f1f1;
    --card: #222226;
    --red: #eb2a2f;
    --white: #ffffff;
    --mark-dark: #1a1a1d;
  }
  * { box-sizing: border-box; margin: 0; padding: 0; }
  html, body { width: 1200px; height: 990px; overflow: hidden; }
  body {
    background: var(--page);
    font-family: "Poppins", sans-serif;
    color: var(--white);
    position: relative;
  }
  .card {
    position: absolute;
    left: 244px;
    width: 712px;
    height: 407px;
    background: var(--card);
    overflow: hidden;
  }
  .card--back { top: 68px; }
  .card--front { top: 515px; }

  /* Back side */
  .brand-emboss {
    position: absolute;
    left: 0; right: 0; top: 160px;
    text-align: center;
    font-weight: 600;
    font-size: 34px;
    letter-spacing: 1px;
    color: var(--mark-dark);
  }
  .brand-emboss .brand-square {
    display: inline-block;
    width: 22px; height: 22px;
    background: var(--mark-dark);
    margin-right: 14px;
    vertical-align: -1px;
  }
  .back-lines {
    position: absolute;
    left: 0; right: 0; top: 333px;
    text-align: center;
    font-size: 16.5px;
    line-height: 22px;
    letter-spacing: 0.4px;
  }
  .back-lines .family { color: var(--red); }

  /* Front side */
  .brand {
    position: absolute;
    left: 26px; top: 70px;
    width: 222px;
    font-weight: 600;
    font-size: 27px;
    line-height: 32px;
    color: var(--white);
  }
  .brand .brand-square {
    display: block;
    width: 26px; height: 26px;
    background: var(--red);
    margin-bottom: 10px;
  }
  .person {
    position: absolute;
    right: 29px; top: 26px;
    text-align: right;
  }
  .person-name {
    font-size: 38px;
    line-height: 44px;
    font-weight: 400;
    letter-spacing: 0.5px;
  }
  .person-name .first { color: var(--red); font-weight: 600; }
  .person-role { font-size: 19px; line-height: 24px; font-weight: 500; letter-spacing: 0.5px; }
  .accent-bar {
    position: absolute;
    right: 0; top: 32px;
    width: 19px; height: 54px;
    background: var(--red);
  }
  .address {
    position: absolute;
    left: 27px; top: 205px;
    font-size: 19.5px;
    line-height: 26px;
    letter-spacing: 0.4px;
  }
  .contact-band {
    position: absolute;
    left: 0; top: 270px;
    width: 712px; height: 137px;
  }
  .contact-list {
    position: absolute;
    left: 26px; top: 287px;
    list-style: none;
    font-size: 19px;
    line-height: 24.3px;
    letter-spacing: 0.4px;
  }
  .contact-list li { display: flex; align-items: center; }
  .contact-list svg { width: 16px; height: 16px; margin-right: 9px; flex: none; }
</style>
</head>
<body>

  <section class="card card--back" aria-label="Card back">
    <div class="brand-emboss"><span class="brand-square"></span>Marlow Estate Fixers</div>
    <p class="back-lines">
      <span class="family">Family Owned and Operated</span><br>
      Your trusted team for all of your Handyman and Home Improvement needs
    </p>
  </section>

  <section class="card card--front" aria-label="Card front">
    <div class="brand"><span class="brand-square"></span>Marlow Estate Fixers</div>

    <div class="person">
      <p class="person-name"><span class="first">Dana</span> Kovar</p>
      <p class="person-role">Founder &amp; CEO</p>
    </div>
    <div class="accent-bar"></div>

    <p class="address">418 Linden Ave. Suite 120<br>Ashford, TX 75012</p>

    <svg class="contact-band" viewBox="0 0 712 137" preserveAspectRatio="none" aria-hidden="true">
      <polygon points="0,0 557,0 474,137 0,137" fill="var(--red)"/>
    </svg>

    <ul class="contact-list">
      <li>
        <svg viewBox="0 0 16 16" aria-hidden="true"><rect x="4" y="1" width="8" height="14" rx="1.5" fill="none" stroke="#fff" stroke-width="1.4"/><line x1="7" y1="12.5" x2="9" y2="12.5" stroke="#fff" stroke-width="1.2"/></svg>
        (555) 214-3086
      </li>
      <li>
        <svg viewBox="0 0 16 16" aria-hidden="true"><path d="M3 2 L6 2 L7 5 L5.5 6.5 C6.5 8.5 7.5 9.5 9.5 10.5 L11 9 L14 10 L14 13 C9 14 2 7 3 2 Z" fill="none" stroke="#fff" stroke-width="1.3" stroke-linejoin="round"/></svg>
        (555) 870-4412
      </li>
      <li>
        <svg viewBox="0 0 16 16" aria-hidden="true"><circle cx="8" cy="8" r="6.5" fill="none" stroke="#fff" stroke-width="1.3"/><ellipse cx="8" cy="8" rx="3" ry="6.5" fill="none" stroke="#fff" stroke-width="1.1"/><line x1="1.5" y1="8" x2="14.5" y2="8" stroke="#fff" stroke-width="1.1"/></svg>
        www.marlowfixers.com
      </li>
      <li>
        <svg viewBox="0 0 16 16" aria-hidden="true"><rect x="1.5" y="3.5" width="13" height="10" fill="none" stroke="#fff" stroke-width="1.3"/><polyline points="1.5,3.5 8,9 14.5,3.5" fill="none" stroke="#fff" stroke-width="1.3"/></svg>
        info@marlowfixers.com
      </li>
    </ul>
  </section>

</body>
</html>
```